Web design - holistic filmmaker

I need a design for my new website.

I am a holistic filmmaker, ie I make films for healers, alternative practitioners, spiritual people and institutions that offer training in this field.

The design should be noble, bright, convey the feeling of space and expanse and have some particularly beautiful color accents.

The structure is: start page, offer, references, about me, imprint.

As an idea for the start page, I thought that either I could introduce myself as a filmmaker and my offer, or we could start right on the start page with the references, ie photos and links to already realized projects.

If you want more information or an exchange, I'd love to hear from you. At the moment I just don't know how to describe it better.

The winner will then be asked to design a logo.

Target Market(s)

healers, alternative practitioners, spiritual people and institutions that offer training in this field

Industry/Entity Type

Film production

Number of Pages Required

3 page

```html
<!DOCTYPE html>
<html lang="en">
<head>
<meta charset="utf-8">
<title>Lennart – Holistic Filmmaker</title>
<link rel="stylesheet" href="https://fonts.googleapis.com/css2?family=Montserrat:wght@400;500;600;700;800&display=swap">
<style>
:root{
  --hero-dark:#0f1f12;
  --hero-mid:#1d3a22;
  --lime:#d6f86a;
  --lime-soft:#f1fdd9;
  --lime-line:#dff09a;
  --green:#3b8a2e;
  --green-btn:#2f8f3a;
  --mint:#6fd6a0;
  --teal:#5fcfd0;
  --text:#333;
  --grey-panel:#f3f3f3;
  --white:#fff;
}
*{margin:0;padding:0;box-sizing:border-box}
html,body{width:1200px;height:2489px;overflow:hidden;background:var(--white)}
body{font-family:'Montserrat',sans-serif;color:var(--text);position:relative}
.abs{position:absolute}

/* hero */
.hero{left:0;top:0;width:1200px;height:657px;background:radial-gradient(ellipse at 75% 45%,#2c4a2a 0%,var(--hero-mid) 40%,var(--hero-dark) 100%);overflow:hidden}
.hero-portrait{left:580px;top:60px;width:620px;height:597px;background:radial-gradient(ellipse at 50% 45%,#c9a58f 0%,#8a7466 40%,rgba(60,70,55,.6) 70%,rgba(30,50,30,0) 100%)}
.nav{left:0;top:13px;width:1200px;height:20px;font-size:13px;color:var(--lime)}
.nav a{position:absolute;color:inherit;text-decoration:none}
.headline{left:56px;top:205px;font-size:57px;line-height:61px;font-weight:400;color:var(--white)}
.headline strong{color:var(--lime);font-weight:700}
.headline .underline{border-bottom:3px solid var(--lime);padding-bottom:2px}
.tagline{left:61px;top:361px;font-size:18px;line-height:21px;color:var(--white)}
.btn{display:flex;align-items:center;justify-content:center;font-size:19px;color:var(--green-btn);border:2px solid var(--green-btn);background:transparent}
.hero .btn{left:62px;top:439px;width:176px;height:51px;color:var(--lime);border-color:var(--mint)}
.band{left:0;top:657px;width:1200px;height:16px;background:linear-gradient(90deg,#d8ecc8 0%,#ffffff 15%,#b2ecec 40%,var(--teal) 70%,#7ddf8a 100%)}

/* cards */
.card{top:788px;width:343px;height:458px;border:2px solid var(--lime-line)}
.card-inner{position:absolute;left:0;right:0;top:14px;bottom:16px;background:var(--lime-soft)}
.card.active .card-inner{background:var(--lime)}
.card-media{position:absolute;left:20px;top:21px;width:302px;height:210px}
.play{position:absolute;left:111px;top:77px;width:80px;height:56px;border-radius:12px;background:rgba(230,30,20,.8)}
.play::after{content:"";position:absolute;left:32px;top:17px;border-left:20px solid rgba(255,255,255,.6);border-top:11px solid transparent;border-bottom:11px solid transparent}
.card h3{position:absolute;left:20px;top:256px;font-size:23px;font-weight:700;color:var(--green)}
.card p{position:absolute;left:20px;width:305px;font-size:13.3px;line-height:16px;color:#444}
.card .p1{top:303px}.card .p2{top:364px}
.cards-btn{left:503px;top:1310px;width:176px;height:51px}

/* about */
.about-accent{left:503px;top:1431px;width:126px;height:456px;background:var(--lime)}
.about-panel{left:629px;top:1431px;width:571px;height:456px;background:var(--grey-panel)}
.about-photo{left:0;top:1476px;width:591px;height:364px;background:linear-gradient(135deg,#e4e4e4 0%,#8d8d8d 45%,#3a3a3a 100%)}
.about-title{left:681px;top:1470px;font-size:38px;line-height:46px;font-weight:700;color:var(--green)}
.about-title .soft{color:var(--lime);background:linear-gradient(90deg,#a7d96a,var(--lime));-webkit-background-clip:text;background-clip:text;color:transparent}
.about-text{left:681px;top:1646px;width:460px;font-size:20.5px;line-height:24px;color:#444}
.about-text strong{color:var(--green);font-weight:600}
.about-text p+p{margin-top:24px}

/* clients */
.clients-title{left:0;top:1982px;width:1135px;text-align:center;font-size:36px;font-weight:800;color:#111}
.client{display:flex;align-items:center;justify-content:center;gap:10px;font-size:22px;font-weight:600;color:#444}
.client .dot{width:14px;height:14px;border-radius:50%;background:var(--green)}
</style>
</head>
<body>

<section class="hero abs">
  <div class="hero-portrait abs" role="img" aria-label="Portrait of the filmmaker in front of a softly glowing green background with a faint geometric pattern"></div>
  <nav class="nav abs">
    <a href="#" style="left:61px">Home</a>
    <a href="#" style="left:592px">Offer</a>
    <a href="#" style="left:734px">References</a>
    <a href="#" style="left:916px">About Me</a>
    <a href="#" style="left:1089px">Imprint</a>
  </nav>
  <h1 class="headline abs">My name is <strong>Lennart</strong><br>and I do <span class="underline">movies</span></h1>
  <p class="tagline abs">A holistic filmmaker filled with<br>enthusiasm and wholeheartedness</p>
  <a class="btn abs" href="#">Read More</a>
</section>
<div class="band abs"></div>

<article class="card abs" style="left:66px">
  <div class="card-inner">
    <div class="card-media" role="img" aria-label="Video still of a woman presenting in front of a flipchart" style="background:linear-gradient(135deg,#8a6a5a,#c06090 55%,#5a4a40)"><span class="play"></span></div>
    <h3>Title Goes Here</h3>
    <p class="p1">Lorem ipsum dolor sit amet, consectetur adipiscing elit, sed do eiusmod tempor incididunt ut labore et dolore magna aliqua.</p>
    <p class="p2">Quis ipsum suspendisse ultrices gravida. Risus commodo viverra maecenas accumsan lacus vel facilisis.</p>
  </div>
</article>
<article class="card abs" style="left:430px">
  <div class="card-inner">
    <div class="card-media" role="img" aria-label="Video still of a healing session with practitioners and a resting client" style="background:linear-gradient(135deg,#4a5a3a,#8a7a6a 45%,#c84a4a)"><span class="play"></span></div>
    <h3>Title Goes Here</h3>
    <p class="p1">Lorem ipsum dolor sit amet, consectetur adipiscing elit, sed do eiusmod tempor incididunt ut labore et dolore magna aliqua.</p>
    <p class="p2">Quis ipsum suspendisse ultrices gravida. Risus commodo viverra maecenas accumsan lacus vel facilisis.</p>
  </div>
</article>
<article class="card active abs" style="left:794px">
  <div class="card-inner">
    <div class="card-media" role="img" aria-label="Video still of a woman under a blue sky beside a tower" style="background:linear-gradient(180deg,#4a7ac0,#8ab0d8 60%,#5a4a40)"><span class="play"></span></div>
    <h3>Title Goes Here</h3>
    <p class="p1">Lorem ipsum dolor sit amet, consectetur adipiscing elit, sed do eiusmod tempor incididunt ut labore et dolore magna aliqua.</p>
    <p class="p2">Quis ipsum suspendisse ultrices gravida. Risus commodo viverra maecenas accumsan lacus vel facilisis.</p>
  </div>
</article>
<a class="btn cards-btn abs" href="#">Read More</a>

<section>
  <div class="about-accent abs"></div>
  <div class="about-panel abs"></div>
  <div class="about-photo abs" role="img" aria-label="Black and white photo of the filmmaker laughing, overlaid with a faint teal ornament"></div>
  <h2 class="about-title abs">Making a movie<br>is always a journey<br><span class="soft">into yourself</span></h2>
  <div class="about-text abs">
    <p><strong>Stillwater Films</strong> is aimed at all people and institutions whose striving for truthfuness is the driving force behind their actions.</p>
    <p>I accompany you on te way to prtraying your essence; with simple means and without special effects.</p>
  </div>
</section>

<section>
  <h2 class="clients-title abs">KUNDEN</h2>
  <div class="client abs" style="left:353px;top:2087px;width:180px;height:116px">Lumen Tal</div>
  <div class="client abs" style="left:618px;top:2087px;width:200px;height:116px"><span class="dot"></span>korvia.de</div>
  <div class="client abs" style="left:367px;top:2260px;width:145px;height:155px">Mira Quell</div>
  <div class="client abs" style="left:607px;top:2260px;width:160px;height:155px">Elbfeld Bühne</div>
</section>

</body>
</html>
```